Single-sided business card for restaurant velmora with new logo made on this site

Business card options with new logo including restaurant name, address, phone number and website. This business card is single-sided only and will be presented at the hostess desk for clients to take. I would like to see options based on a cream card background, a white card background, a yellow card background and a burgundy colored background. It needs to be elegant and traditional.

Target Market(s)

local and international crowd

Industry/Entity Type

restaurant

Contact Information for Business Card

address, website and phone number

Font styles to use
Serif

Colors
EE7325
F08F49
F5BC92
FAE3D3
FDF4ED

Requirements
Must have
• new logo, address, phone number, website
Should not have
• more than three colors

```html
<!DOCTYPE html>
<html lang="es">
<head>
<meta charset="utf-8">
<title>Velmora – business card options</title>
<link rel="stylesheet" href="https://fonts.googleapis.com/css2?family=Tinos:wght@400&family=Didact+Gothic&display=swap">
<style>
  :root {
    --page: #ffffff;
    --burgundy: #3f1f1f;
    --yellow: #f5b335;
    --cream: #ffffcc;
    --white: #ffffff;
    --ink-dark: #111111;
    --ink-light: #f4eee6;
    --band: #000000;
    --band-text: #ffffff;
  }
  * { margin: 0; padding: 0; box-sizing: border-box; }
  html, body { width: 1200px; height: 1117px; overflow: hidden; background: var(--page); }
  .sheet { position: relative; width: 1200px; height: 1117px; }

  .card {
    position: absolute; width: 532px; height: 325px;
    background: var(--bg); color: var(--ink);
    font-family: "Tinos", "Times New Roman", serif;
  }
  .card--burgundy { left: 43px; top: 142px; --bg: var(--burgundy); --ink: var(--ink-light); --mark: var(--ink-light); --icon-glyph: var(--burgundy); }
  .card--yellow   { left: 624px; top: 142px; --bg: var(--yellow); --ink: var(--burgundy); --mark: var(--burgundy); --icon-glyph: var(--yellow); }
  .card--white    { left: 43px; top: 493px; --bg: var(--white); --ink: var(--ink-dark); --mark: var(--ink-dark); --icon-glyph: var(--white); border: 1px solid #555; }
  .card--cream    { left: 624px; top: 493px; --bg: var(--cream); --ink: var(--ink-dark); --mark: var(--ink-dark); --icon-glyph: var(--cream); }

  .brand { position: absolute; left: 38px; top: 92px; width: 160px; text-align: center; }
  .brand__square { display: block; width: 78px; height: 77px; margin: 0 auto; background: var(--mark); }
  .brand__name {
    margin-top: 16px; font-size: 27px; letter-spacing: 4px; line-height: 1; color: var(--ink);
  }

  .divider { position: absolute; left: 202px; top: 46px; width: 6px; height: 234px; }
  .divider polygon { fill: var(--ink); }

  .details { position: absolute; left: 234px; top: 82px; }
  .details__title { font-size: 28px; line-height: 28px; letter-spacing: 0.3px; }
  .contact { list-style: none; margin-top: 17px; }
  .contact li { display: flex; align-items: center; gap: 7px; font-size: 14px; line-height: 21px; }
  .contact svg { width: 14px; height: 14px; flex: none; }
  .contact .icon-bg { fill: var(--ink); }
  .contact .icon-glyph { fill: var(--icon-glyph); stroke: var(--icon-glyph); }

  .note-band {
    position: absolute; left: 0; top: 960px; width: 1200px; height: 157px;
    background: var(--band); color: var(--band-text);
    font-family: "Didact Gothic", "Helvetica", sans-serif; font-size: 21px;
  }
  .note-band__fragment { position: absolute; left: 591px; top: 18px; }
  .note-band__message { position: absolute; left: 28px; top: 42px; }
</style>
</head>
<body>
<svg width="0" height="0" style="position:absolute" aria-hidden="true">
  <defs>
    <symbol id="icon-home" viewBox="0 0 14 14">
      <circle class="icon-bg" cx="7" cy="7" r="7"/>
      <path class="icon-glyph" stroke="none" d="M7 3 L11 6.6 H9.8 V10.5 H8 V8 H6 V10.5 H4.2 V6.6 H3 Z"/>
    </symbol>
    <symbol id="icon-phone" viewBox="0 0 14 14">
      <circle class="icon-bg" cx="7" cy="7" r="7"/>
      <path class="icon-glyph" stroke="none" d="M3.2 5.6 Q7 3 10.8 5.6 L10.3 6.8 L8.8 6.4 L8.6 5.5 Q7 5 5.4 5.5 L5.2 6.4 L3.7 6.8 Z M4.4 7.6 H9.6 L10 10.4 H4 Z"/>
    </symbol>
    <symbol id="icon-web" viewBox="0 0 14 14">
      <circle class="icon-bg" cx="7" cy="7" r="7"/>
      <g class="icon-glyph" fill="none" stroke-width="0.9">
        <circle cx="7" cy="7" r="3.8" fill="none"/>
        <ellipse cx="7" cy="7" rx="1.6" ry="3.8" fill="none"/>
        <line x1="3.2" y1="7" x2="10.8" y2="7"/>
      </g>
    </symbol>
  </defs>
</svg>

<main class="sheet">
  <!-- Four colourways of the same card layout -->
  <section class="card card--burgundy">
    <div class="brand"><span class="brand__square"></span><p class="brand__name">VELMORA</p></div>
    <svg class="divider" viewBox="0 0 6 234" preserveAspectRatio="none" aria-hidden="true"><polygon points="3,0 5,117 3,234 1,117"/></svg>
    <div class="details">
      <h1 class="details__title">Restaurant<br>Velmora<br>Magnolia 415</h1>
      <ul class="contact">
        <li><svg><use href="#icon-home"/></svg>Bahías del Sol, Oaxaca CP 70930</li>
        <li><svg><use href="#icon-phone"/></svg>Reservaciones 958-555-0142</li>
        <li><svg><use href="#icon-web"/></svg>www.velmora.com.mx</li>
      </ul>
    </div>
  </section>

  <section class="card card--yellow">
    <div class="brand"><span class="brand__square"></span><p class="brand__name">VELMORA</p></div>
    <svg class="divider" viewBox="0 0 6 234" preserveAspectRatio="none" aria-hidden="true"><polygon points="3,0 5,117 3,234 1,117"/></svg>
    <div class="details">
      <h1 class="details__title">Restaurant<br>Velmora<br>Magnolia 415</h1>
      <ul class="contact">
        <li><svg><use href="#icon-home"/></svg>Bahías del Sol, Oaxaca CP 70930</li>
        <li><svg><use href="#icon-phone"/></svg>Reservaciones 958-555-0142</li>
        <li><svg><use href="#icon-web"/></svg>www.velmora.com.mx</li>
      </ul>
    </div>
  </section>

  <section class="card card--white">
    <div class="brand"><span class="brand__square"></span><p class="brand__name">VELMORA</p></div>
    <svg class="divider" viewBox="0 0 6 234" preserveAspectRatio="none" aria-hidden="true"><polygon points="3,0 5,117 3,234 1,117"/></svg>
    <div class="details">
      <h1 class="details__title">Restaurant<br>Velmora<br>Magnolia 415</h1>
      <ul class="contact">
        <li><svg><use href="#icon-home"/></svg>Bahías del Sol, Oaxaca CP 70930</li>
        <li><svg><use href="#icon-phone"/></svg>Reservaciones 958-555-0142</li>
        <li><svg><use href="#icon-web"/></svg>www.velmora.com.mx</li>
      </ul>
    </div>
  </section>

  <section class="card card--cream">
    <div class="brand"><span class="brand__square"></span><p class="brand__name">VELMORA</p></div>
    <svg class="divider" viewBox="0 0 6 234" preserveAspectRatio="none" aria-hidden="true"><polygon points="3,0 5,117 3,234 1,117"/></svg>
    <div class="details">
      <h1 class="details__title">Restaurant<br>Velmora<br>Magnolia 415</h1>
      <ul class="contact">
        <li><svg><use href="#icon-home"/></svg>Bahías del Sol, Oaxaca CP 70930</li>
        <li><svg><use href="#icon-phone"/></svg>Reservaciones 958-555-0142</li>
        <li><svg><use href="#icon-web"/></svg>www.velmora.com.mx</li>
      </ul>
    </div>
  </section>

  <footer class="note-band">
    <p class="note-band__fragment">ange.</p>
    <p class="note-band__message">Any feedback/ rating would be very helpfull.</p>
  </footer>
</main>
</body>
</html>
```